Sleek wordpress site for Bramblecrest finishing works

We are a commercial job shop that serves B2B, govt & LEO and retail clients.We need a wordpress site with 6 individual pages: homepage, coating, laser engraving, laser cutting, part marking, and contact us. I have attached an outline of the desired flow and sub headings for each page. I would like to incorporate the colors of the logo through out the site to be clean and sleek enough to appeal to B2B commercial clients yet be inviting enough for retail clients.

I would like to have easy picture functionality so photographs on each page can be updated easily.

Target Market(s)

B2B industrial & Govt and Military part marking, laser engraving and coating: machine shops, aerospace companies, tool manufactures. Retail: personalized gifts, Job Shop

Coding

Coded - Design and coding required

Font styles to use
Sans Serif
Other font styles liked:
• Open to suggestion

Colors
0255a3
3176b5
eaf1f7
cfdeed
ffffff

Requirements
Must have
• Clean easy to navigate flow, separate pages as indicated on attached outline, high class feel. Great picture functionality, professional and inviting feel,
• **update: needs to be optimized for mobile, should have a gallery function. Gallery can be an additional page or embedded
Nice to have
• Social media connectivity links,
Should not have
• crappy plugins that make back-end management difficult, no blog

```html
<!DOCTYPE html>
<html lang="en">
<head>
<meta charset="utf-8">
<title>Bramblecrest Finishing Works</title>
<link href="https://fonts.googleapis.com/css2?family=Roboto:ital,wght@0,400;0,500;0,700;1,400&family=Roboto+Condensed:wght@700&family=Poppins:wght@400;500&display=swap" rel="stylesheet">
<style>
:root{
  --blue:#0255a3;
  --blue-mid:#3176b5;
  --blue-deep:#0b3a86;
  --blue-pale:#eaf1f7;
  --blue-soft:#cfdeed;
  --white:#ffffff;
  --ink:#3a3a3a;
  --dark:#1b1b1b;
}
*{margin:0;padding:0;box-sizing:border-box}
html,body{width:1200px;height:3364px;overflow:hidden}
body{font-family:"Roboto",sans-serif;color:var(--ink);background:var(--white);position:relative}
.abs{position:absolute}
/* header */
.brand{left:130px;top:22px;width:230px}
.brand-mark{width:48px;height:48px;border-radius:50%;background:var(--blue);margin:0 auto 10px 60px}
.brand-name{font-weight:700;font-size:18px;color:var(--blue);line-height:1.15;text-transform:uppercase}
.contact-head{left:520px;top:28px;display:flex;gap:22px;align-items:center}
.contact-head .num{font-weight:700;font-size:19px;color:#222}
.contact-head .mail{font-size:14px;color:#333;margin-top:4px}
.search{left:830px;top:32px;width:236px;height:36px;border:1px solid #ccc;border-radius:18px;font-size:12px;color:#999;padding:10px 16px}
.search svg{position:absolute;right:12px;top:9px}
.nav{left:359px;top:105px;width:841px;height:50px;background:var(--blue);clip-path:polygon(18px 0,100% 0,100% 100%,0 100%)}
.nav ul{list-style:none;display:flex;height:100%}
.nav li{font-family:"Roboto Condensed",sans-serif;font-size:14px;color:var(--white);line-height:50px;padding:0 26px;letter-spacing:.3px}
.nav li.active{background:#1c1c1c;padding:0 30px 0 38px}
/* hero */
.hero{left:0;top:155px;width:1200px;height:630px;background:radial-gradient(circle at 33% 78%,#c98a3c 0,#6b4a2a 12%,#2c2a28 34%,#161616 70%)}
.hero-title{left:718px;top:375px;font-family:"Roboto Condensed",sans-serif;font-size:52px;color:var(--white)}
.hero-text{left:720px;top:452px;width:330px;font-size:14px;font-weight:500;line-height:23px;color:var(--white)}
.btn-outline{border:2px solid var(--white);border-radius:20px;color:var(--white);font-weight:700;font-size:14px;padding:8px 24px;display:inline-block}
.hero-btn{left:720px;top:546px}
.hero-curve{left:0;top:640px}
/* services */
.services{left:0;top:785px;width:1200px;height:595px;background:linear-gradient(180deg,#fff 0,#f3f3f3 40%,#dcdcdc 100%)}
.section-title{left:0;width:1200px;text-align:center;font-size:38px;font-weight:700;color:#3b3b3b;letter-spacing:.5px}
.section-title span{color:var(--blue)}
.svc{width:290px}
.svc h3{font-size:21px;font-weight:500;color:var(--blue);margin-bottom:12px}
.svc p{font-family:"Poppins",sans-serif;font-size:11.5px;line-height:24px;color:#444}
.svc.left{text-align:right}
.svc-icon{width:112px;height:112px;border-radius:50%;background:var(--blue);border:4px solid #1f1f1f;box-shadow:0 0 0 3px #fff inset;display:flex;align-items:center;justify-content:center}
/* welcome */
.welcome{left:0;top:1380px;width:1200px;height:515px;background:linear-gradient(120deg,#131313 0,#2a2520 45%,#4a3420 70%,#1a1a1a 100%)}
.welcome-title{left:132px;top:1470px;font-size:31px;font-weight:500;color:var(--white);line-height:42px}
.welcome-text{left:132px;top:1568px;width:470px;font-size:12.5px;line-height:26px;color:#eee}
.welcome-btn{left:132px;top:1750px;border:2px solid #fff;color:#fff;font-weight:700;font-size:13px;padding:7px 12px}
.video{left:640px;top:1475px;width:426px;height:318px;border:2px solid #8a8a8a;padding:10px}
.video-img{width:100%;height:100%;background:linear-gradient(135deg,#6d7d8f,#b8c1c9 50%,#5f6a78)}
.play{left:822px;top:1614px;width:62px;height:62px;border-radius:50%;background:#fff;display:flex;align-items:center;justify-content:center}
/* news */
.card{width:292px}
.card-img{height:183px;background:linear-gradient(135deg,#2a2a2a,#7a7a80 50%,#b33)}
.card-img.b{background:linear-gradient(160deg,#222,#9aa 55%,#555)}
.card-img.c{background:linear-gradient(120deg,#9aa0a8,#d9782a 60%,#5b5b5b)}
.card-body{margin-top:22px;border-left:4px solid #555;padding-left:16px}
.card-date{font-size:13px;color:#444;margin-bottom:10px}
.card-title{font-size:14.5px;line-height:21px;color:var(--blue-deep)}
/* testimonials */
.testimonials{left:0;top:2467px;width:1200px;height:500px;background:var(--blue-pale)}
.arrow{top:2676px}
.client-photo{left:188px;top:2624px;width:170px;height:170px;border-radius:50%;background:linear-gradient(135deg,#5c6b7c,#a9b2bb);border:4px solid var(--blue);box-shadow:0 0 0 5px #fff inset}
.quote{left:437px;top:2614px;width:600px;font-size:17px;font-style:italic;line-height:30px;color:#555}
.client-name{left:437px;top:2752px;font-size:16px;line-height:27px;color:#222}
.qmark{font-family:Georgia,serif;font-size:110px;color:#bfc6cd;line-height:1}
/* footer */
.footer{left:0;top:2890px;width:1200px;height:474px;background:var(--blue-deep)}
.foot-h{font-size:22px;font-weight:700;color:#fff}
.foot-list{list-style:none;font-size:12.5px;color:#e6eefa}
.foot-list li{display:flex;gap:14px;align-items:flex-start;margin-bottom:22px;line-height:19px}
.links{list-style:none;font-size:12px;color:#fff}
.links li{margin-bottom:9px;display:flex;align-items:center;gap:14px}
.links li::before{content:"";width:7px;height:7px;border-radius:50%;background:#fff}
.email-field{left:682px;top:3070px;width:257px;height:38px;background:#fff;font-size:12px;color:#777;padding:11px 12px}
.sub-btn{left:953px;top:3070px;width:112px;height:38px;background:#3d3d3d;color:#fff;font-size:13px;font-weight:700;line-height:38px;text-align:center}
.social{width:16px;height:16px;background:#fff;border-radius:2px}
.copy{left:0;top:3272px;width:1200px;border-top:1px solid rgba(255,255,255,.2);padding-top:34px;text-align:center;font-size:12px;color:#fff}
</style>
</head>
<body>

<header>
  <div class="abs brand">
    <div class="brand-mark"></div>
    <div class="brand-name">Bramblecrest Finishing Works</div>
  </div>
  <div class="abs contact-head">
    <svg width="26" height="30" viewBox="0 0 24 24"><path fill="#0b3a86" d="M6.6 10.8a15.1 15.1 0 0 0 6.6 6.6l2.2-2.2c.3-.3.7-.4 1-.2 1.1.4 2.3.6 3.6.6.6 0 1 .4 1 1V20c0 .6-.4 1-1 1A17 17 0 0 1 3 4c0-.6.4-1 1-1h3.5c.6 0 1 .4 1 1 0 1.3.2 2.5.6 3.6.1.3 0 .7-.2 1z"/></svg>
    <div><div class="num">555.014.2290</div><div class="mail">hello@bramblecrestworks.com</div></div>
  </div>
  <div class="abs search">Search here
    <svg width="16" height="16" viewBox="0 0 24 24"><circle cx="10" cy="10" r="7" stroke="#777" stroke-width="2.5" fill="none"/><path d="M15 15l6 6" stroke="#777" stroke-width="2.5"/></svg>
  </div>
  <nav class="abs nav"><ul>
    <li class="active">HOME</li><li>COATING</li><li>LASER ENGRAVING</li><li>LASER CUTTING</li><li>PART MARKING</li><li>CONTACT</li>
  </ul></nav>
</header>

<section>
  <div class="abs hero" role="img" aria-label="Laser cutting head throwing sparks across a metal sheet"></div>
  <svg class="abs hero-curve" width="1200" height="160" viewBox="0 0 1200 160">
    <path d="M0 40 Q600 190 1200 40 L1200 160 L0 160 Z" fill="#fff"/>
    <path d="M55 70 Q600 180 1145 70" stroke="#0b3a86" stroke-width="7" fill="none"/>
    <path d="M40 62 Q600 168 1160 62" stroke="#1c1c1c" stroke-width="2" fill="none"/>
    <circle cx="575" cy="92" r="8" fill="#fff" stroke="#bbb"/>
    <circle cx="601" cy="92" r="7" fill="none" stroke="#888" stroke-width="1.5"/>
    <circle cx="627" cy="92" r="7" fill="none" stroke="#888" stroke-width="1.5"/>
  </svg>
  <h1 class="abs hero-title">LASER CUTTING</h1>
  <p class="abs hero-text">Sed ut perspiciatis unde omnis iste natus error sit voluptatem accusantium doloremque laudantium, totam rem aperiam, eaque ipsa quae</p>
  <span class="abs btn-outline hero-btn">GET MORE INFO</span>
</section>

<section>
  <div class="abs services" role="img" aria-label="Faded workshop background with a technician at a machine"></div>
  <h2 class="abs section-title" style="top:862px">OUR <span>SERVICES</span></h2>

  <div class="abs svc left" style="left:140px;top:963px"><h3>Laser Engraving</h3><p>Sed ut perspiciatis unde omnis iste natus error sit voluptatem accusantium doloremque laudantium, totam rem aperiam, eaque ipsa quae ab illo inventore veritatis et quasi architecto</p></div>
  <div class="abs svc-icon" style="left:459px;top:979px"><svg width="56" height="56" viewBox="0 0 56 56" fill="none" stroke="#fff" stroke-width="3"><path d="M14 10h28l-6 12H20z"/><path d="M28 22v10"/><path d="M8 44h40M14 38h28"/></svg></div>
  <div class="abs svc-icon" style="left:627px;top:979px"><svg width="56" height="56" viewBox="0 0 56 56" fill="none" stroke="#fff" stroke-width="3"><rect x="18" y="6" width="20" height="16"/><path d="M22 22l6 12 6-12"/><path d="M28 36v4M20 46h16M12 48h6M38 48h6"/></svg></div>
  <div class="abs svc" style="left:771px;top:963px"><h3>Laser Cutting</h3><p>Sed ut perspiciatis unde omnis iste natus error sit voluptatem accusantium doloremque laudantium, totam rem aperiam, eaque ipsa quae ab illo inventore veritatis et quasi architecto</p></div>

  <div class="abs svc left" style="left:140px;top:1143px"><h3>Part Marking</h3><p>Sed ut perspiciatis unde omnis iste natus error sit voluptatem accusantium doloremque laudantium, totam rem aperiam, eaque ipsa quae ab illo inventore veritatis et quasi architecto</p></div>
  <div class="abs svc-icon" style="left:459px;top:1159px"><svg width="56" height="56" viewBox="0 0 56 56" fill="none" stroke="#fff" stroke-width="3"><rect x="22" y="8" width="12" height="40" rx="3"/><path d="M8 24h14M34 24h14M8 32h14M34 32h14"/></svg></div>
  <div class="abs svc-icon" style="left:627px;top:1159px"><svg width="56" height="56" viewBox="0 0 56 56" fill="none" stroke="#fff" stroke-width="3"><rect x="10" y="10" width="30" height="12" rx="2"/><path d="M40 16h6v12H26v8"/><rect x="22" y="36" width="8" height="12"/></svg></div>
  <div class="abs svc" style="left:771px;top:1143px"><h3>Coatings</h3><p>Sed ut perspiciatis unde omnis iste natus error sit voluptatem accusantium doloremque laudantium, totam rem aperiam, eaque ipsa quae ab illo inventore veritatis et quasi architecto</p></div>
</section>

<section>
  <div class="abs welcome" role="img" aria-label="Dark workshop scene with grinding sparks"></div>
  <h2 class="abs welcome-title">WELCOME TO<br>BRAMBLECREST FINISHING</h2>
  <p class="abs welcome-text">Sed ut perspiciatis unde omnis iste natus error sit voluptatem accusantium doloremque laudantium, totam rem aperiam, eaque ipsa quae ab illo inventore veritatis et quasi architecto beatae vitae dicta sunt explicabo. Nemo enim ipsam voluptatem quia voluptas sit aspernatur aut odit aut fugit, sed quia consequuntur magni dolores eos qui ratione voluptatem sequi nesciunt. Neque porro quisquam est, qui dolorem ipsum</p>
  <span class="abs welcome-btn">READ MORE</span>
  <div class="abs video"><div class="video-img" role="img" aria-label="Video still of two workers inspecting a metal sheet"></div></div>
  <div class="abs play"><svg width="22" height="24" viewBox="0 0 22 24"><path d="M3 2l17 10L3 22z" fill="#1b1b1b"/></svg></div>
</section>

<section>
  <h2 class="abs section-title" style="top:1970px">LATEST <span>NEWS</span></h2>
  <article class="abs card" style="left:132px;top:2082px"><div class="card-img" role="img" aria-label="Laser etching lettering into metal"></div><div class="card-body"><div class="card-date">&#9638;&nbsp; October 17, 2018</div><div class="card-title">Nemo enim ipsam voluptatem quia voluptas sit aspernatur aut odit aut fugit</div></div></article>
  <article class="abs card" style="left:453px;top:2082px"><div class="card-img b" role="img" aria-label="Laser cutter over a perforated steel plate"></div><div class="card-body"><div class="card-date">&#9638;&nbsp; October 17, 2018</div><div class="card-title">Nemo enim ipsam voluptatem quia voluptas sit aspernatur aut odit aut fugit</div></div></article>
  <article class="abs card" style="left:775px;top:2082px"><div class="card-img c" role="img" aria-label="Worker spray coating an orange part"></div><div class="card-body"><div class="card-date">&#9638;&nbsp; October 17, 2018</div><div class="card-title">Nemo enim ipsam voluptatem quia voluptas sit aspernatur aut odit aut fugit</div></div></article>
</section>

<section>
  <div class="abs testimonials"></div>
  <h2 class="abs section-title" style="top:2516px">WHAT <span>OUR CLIENTS</span> SAY</h2>
  <svg class="abs arrow" style="left:84px" width="22" height="34" viewBox="0 0 22 34"><path d="M18 3L5 17l13 14" stroke="#666" stroke-width="4" fill="none"/></svg>
  <svg class="abs arrow" style="left:1094px" width="22" height="34" viewBox="0 0 22 34"><path d="M4 3l13 14L4 31" stroke="#666" stroke-width="4" fill="none"/></svg>
  <div class="abs client-photo" role="img" aria-label="Client portrait"></div>
  <div class="abs qmark" style="left:364px;top:2600px">&ldquo;</div>
  <p class="abs quote">Sed ut perspiciatis unde omnis iste natus error sit voluptatem accusantium doloremque laudantium, totam rem aperiam, eaque ipsa quae ab illo inventore veritatis et quasi architecto beatae vitae dicta sunt explicabo. Nemo enim ipsam voluptatem quia voluptas sit aspernatur aut odit aut fugit</p>
  <p class="abs client-name">Daniel Harlow<br>Bramblecrest Finishing</p>
  <div class="abs qmark" style="left:925px;top:2720px">&rdquo;</div>
</section>

<footer>
  <svg class="abs" style="left:0;top:2835px" width="1200" height="70" viewBox="0 0 1200 70">
    <path d="M40 62 Q600 -30 1160 62" stroke="#1c1c1c" stroke-width="2" fill="none"/>
    <path d="M0 70 Q600 -10 1200 70 Z" fill="#0b3a86"/>
  </svg>
  <div class="abs footer"></div>
  <h3 class="abs foot-h" style="left:132px;top:2975px">CONTACT US</h3>
  <ul class="abs foot-list" style="left:132px;top:3033px;width:260px">
    <li><svg width="16" height="20" viewBox="0 0 16 20"><path d="M8 1a6 6 0 0 1 6 6c0 5-6 12-6 12S2 12 2 7a6 6 0 0 1 6-6z" stroke="#fff" stroke-width="1.6" fill="none"/><circle cx="8" cy="7" r="2" fill="#fff"/></svg><span>Bramblecrest Finishing<br>418 Harrow Lane #12, Fairview,<br>AZ 85011</span></li>
    <li><svg width="16" height="16" viewBox="0 0 24 24"><path fill="#fff" d="M6.6 10.8a15.1 15.1 0 0 0 6.6 6.6l2.2-2.2c.3-.3.7-.4 1-.2 1.1.4 2.3.6 3.6.6.6 0 1 .4 1 1V20c0 .6-.4 1-1 1A17 17 0 0 1 3 4c0-.6.4-1 1-1h3.5c.6 0 1 .4 1 1 0 1.3.2 2.5.6 3.6.1.3 0 .7-.2 1z"/></svg><span>Phone: 555.014.2290</span></li>
    <li><svg width="16" height="16" viewBox="0 0 16 16"><rect x="2" y="5" width="12" height="9" fill="#fff"/><rect x="4" y="1" width="8" height="4" stroke="#fff" fill="none"/></svg><span>Fax: 555.014.2291</span></li>
    <li><svg width="16" height="14" viewBox="0 0 16 14"><rect x="1" y="2" width="14" height="10" stroke="#fff" fill="none" stroke-width="1.5"/><path d="M1 2l7 6 7-6" stroke="#fff" fill="none" stroke-width="1.5"/></svg><span>hello@bramblecrestworks.com</span></li>
  </ul>
  <h3 class="abs foot-h" style="left:460px;top:2975px">QUICK LINKS</h3>
  <ul class="abs links" style="left:463px;top:3033px">
    <li>Home</li><li>coating</li><li>laser engraving</li><li>laser cutting</li><li>part marking</li><li>contact us</li>
  </ul>
  <h3 class="abs foot-h" style="left:682px;top:2975px">SIGN UP FOR NEWSLETTER</h3>
  <p class="abs" style="left:682px;top:3036px;font-size:12px;color:#fff">Sign up to our mailing list</p>
  <div class="abs email-field">Enter email</div>
  <div class="abs sub-btn">SUBSCRIPTION</div>
  <p class="abs" style="left:682px;top:3140px;font-size:12px;font-weight:700;color:#fff">STAY CONNECTED WITH US</p>
  <div class="abs social" style="left:682px;top:3176px"></div>
  <div class="abs social" style="left:704px;top:3176px"></div>
  <p class="abs copy">(c) 2018 Bramblecrest Finishing | All Rights Reserved | Disclaimer</p>
</footer>

</body>
</html>
```